Print materials for 3-star hotel

We are changing up our print materials (notepads, letterheads, key card jackets, small flyer for the room rates) We are a 3 star business hotel in the Philippines and have mainly used grey tones and clean, simple lines. See attached photos for logo and hotel interior photos.

Target Market(s)

Business

Contact Information for Business Card

Corvale Terrace Hotel
Lindwell Banca Avenue corner Tolenta St Cebu City 6000 Philippines
Tel: +63 32 481 7302
Mobile: +63 917 648 2095
www.corvaleterracehotel.example

Font styles to use
Serif
Sans Serif

Requirements
Must have
• Simple
• Readable font and font size
Nice to have
• Neutral colors, grey and taupes
Should not have
• No purples and bright blues

```html
<!DOCTYPE html>
<html lang="en">
<head>
<meta charset="utf-8">
<title>Corvale Terrace Hotel — Business Card</title>
<link rel="stylesheet" href="https://fonts.googleapis.com/css2?family=EB+Garamond:wght@400;500&display=swap">
<style>
  :root {
    --page: #eef0ef;
    --taupe: #a69579;
    --taupe-ink: #9c8a6c;
    --paper: #fbfbfa;
    --white: #ffffff;
    --shadow: rgba(60, 50, 35, 0.14);
  }
  * { margin: 0; padding: 0; box-sizing: border-box; }
  html, body {
    width: 1200px;
    height: 900px;
    overflow: hidden;
    background: var(--page);
    font-family: "EB Garamond", Georgia, serif;
  }
  .sheet {
    width: 1200px;
    height: 900px;
    display: flex;
    align-items: center;
    justify-content: center;
    gap: 48px;
  }
  .card {
    width: 525px;
    height: 300px;
    position: relative;
    box-shadow: 0 10px 28px var(--shadow);
    overflow: hidden;
  }
  .card--front { background: var(--taupe); }
  .card--back { background: var(--paper); }

  .wordmark {
    position: absolute;
    display: flex;
    flex-direction: column;
    align-items: center;
    gap: 14px;
  }
  .card--front .wordmark {
    left: 50%;
    top: 50%;
    transform: translate(-50%, -50%);
    color: var(--white);
  }
  .card--back .wordmark {
    left: 30px;
    width: 220px;
    top: 50%;
    transform: translateY(-50%);
    color: var(--taupe-ink);
  }
  .wordmark__square {
    background: currentColor;
    flex: none;
  }
  .card--front .wordmark__square { width: 40px; height: 40px; }
  .card--back .wordmark__square { width: 30px; height: 30px; }
  .wordmark__name {
    font-weight: 400;
    text-transform: uppercase;
    line-height: 1.3;
    text-align: center;
    white-space: nowrap;
  }
  .wordmark__line { display: block; }
  .card--front .wordmark__name { font-size: 20px; letter-spacing: 0.3em; }
  .card--back .wordmark__name { font-size: 13px; letter-spacing: 0.22em; }

  .contact {
    position: absolute;
    left: 272px;
    right: 22px;
    top: 50%;
    transform: translateY(-50%);
    color: var(--taupe-ink);
    font-size: 13px;
    line-height: 1.35;
  }
  .contact__name {
    font-size: 19px;
    font-weight: 500;
    letter-spacing: 0.04em;
    text-transform: uppercase;
    line-height: 1.1;
  }
  .contact__role { font-size: 14px; margin-bottom: 10px; }
  .contact__block { margin-bottom: 10px; }
</style>
</head>
<body>
  <main class="sheet">
    <section class="card card--front" aria-label="Card front">
      <div class="wordmark">
        <span class="wordmark__square" aria-hidden="true"></span>
        <span class="wordmark__name">
          <span class="wordmark__line">Corvale Terrace</span>
          <span class="wordmark__line">Hotel</span>
        </span>
      </div>
    </section>

    <section class="card card--back" aria-label="Card back">
      <div class="wordmark">
        <span class="wordmark__square" aria-hidden="true"></span>
        <span class="wordmark__name">
          <span class="wordmark__line">Corvale Terrace</span>
          <span class="wordmark__line">Hotel</span>
        </span>
      </div>
      <div class="contact">
        <p class="contact__name">Elias Morrow</p>
        <p class="contact__role">CEO/Founder</p>
        <p class="contact__block">Lindwell Banca Avenue<br>corner Tolenta St<br>Cebu City 6000 Philippines</p>
        <p>t. +63 32 481 7302<br>m. +63 917 648 2095<br>elias@corvaleterracehotel.example<br>www.corvaleterracehotel.example</p>
      </div>
    </section>
  </main>
</body>
</html>
```